Card Design for my dog training business Brightpaw Obedience

Need a business card design for my dog training business with my new logo. Want the card to come off professional yet fun. Want it to be very eye catchy as well. I normally have these at vet clinics, pet stores, and groomers. so need it to look better than my competitors.
Target Market(s)
dog owners
Industry/Entity Type
Dog Training
Contact Information for Business Card
needs logo, my name and info
Font styles to use
Serif
Colors
0255a3
ffffff
ec1f27
000000
333333
fbfbfb
Requirements
Must have
- Brightpaw Obedience
- Felix Orland
- 415 903 2276
- info@brightpawobedience.example
- www.brightpawobedience.example

```html
<!DOCTYPE html>
<html lang="en">
<head>
<meta charset="utf-8">
<title>Brightpaw Obedience – Business Card</title>
<link rel="stylesheet" href="https://fonts.googleapis.com/css2?family=Cinzel:wght@700&family=EB+Garamond:ital@1&family=Roboto:wght@300&display=swap">
<style>
  :root {
    --page-bg: #e4e4e4;
    --card-white: #ffffff;
    --ink: #000000;
    --ink-soft: #333333;
    --rule: #555555;
    --watermark: #f6f6f6;
    --dark-top: #1d1d1d;
    --dark-bottom: #0b0b0b;
    --silver: #a9a9a9;
    --tagline: #8c8c8c;
  }
  * { margin: 0; padding: 0; box-sizing: border-box; }
  html, body {
    width: 1125px; height: 1200px; overflow: hidden;
    background: var(--page-bg);
  }
  .card {
    position: absolute; left: 150px; width: 826px; height: 470px; overflow: hidden;
  }
  .card-front { top: 98px; background: var(--card-white); }
  .card-back {
    top: 631px;
    background: linear-gradient(135deg, var(--dark-top) 0%, var(--dark-bottom) 100%);
  }
  .watermark-art {
    position: absolute; left: 18px; top: 86px; width: 414px; height: 384px;
    background: var(--watermark);
    border-radius: 120px 120px 0 0;
  }
  .brand-mark {
    position: absolute; left: 578px; top: 49px; width: 191px; height: 191px;
    display: flex; flex-direction: column; align-items: center; justify-content: center; gap: 12px;
    font-family: "Cinzel", serif; font-weight: 700; color: var(--ink);
    text-align: center; line-height: 1.1; font-size: 22px;
  }
  .brand-mark .square { width: 34px; height: 34px; background: var(--ink); }
  .accent-bar {
    position: absolute; left: 0; top: 342px; width: 12px; height: 40px; background: var(--ink);
  }
  .person-name {
    position: absolute; left: 56px; top: 344px;
    font-family: "Cinzel", serif; font-weight: 700; font-size: 31px; letter-spacing: 1px;
    color: var(--ink); line-height: 1;
  }
  .name-rule {
    position: absolute; left: 56px; top: 387px; width: 713px; height: 1px; background: var(--rule);
  }
  .contact-list {
    position: absolute; left: 56px; top: 404px; display: flex; align-items: center; gap: 14px;
    font-family: "Roboto", sans-serif; font-weight: 300; font-size: 17px; color: var(--ink-soft);
    list-style: none;
  }
  .contact-list li { display: flex; align-items: center; gap: 5px; white-space: nowrap; }
  .contact-list svg { width: 16px; height: 16px; fill: var(--ink); }
  .back-mark {
    position: absolute; left: 243px; top: 102px; width: 340px; height: 253px;
    display: flex; flex-direction: column; align-items: center; justify-content: center; gap: 18px;
    font-family: "Cinzel", serif; font-weight: 700; color: var(--silver);
    font-size: 36px; line-height: 1.1; text-align: center;
  }
  .back-mark .square { width: 54px; height: 54px; background: var(--silver); }
  .tagline {
    position: absolute; left: 0; right: 0; top: 403px; text-align: center;
    font-family: "EB Garamond", serif; font-style: italic; font-size: 23px; color: var(--tagline);
  }
</style>
</head>
<body>
  <section class="card card-front">
    <div class="watermark-art" role="img" aria-label="Faint large dog-head illustration behind the name"></div>
    <div class="brand-mark">
      <span class="square"></span>
      <span>Brightpaw<br>Obedience</span>
    </div>
    <span class="accent-bar"></span>
    <h1 class="person-name">FELIX ORLAND</h1>
    <span class="name-rule"></span>
    <ul class="contact-list">
      <li>
        <svg viewBox="0 0 24 24" aria-hidden="true"><path d="M6.6 10.8a15.1 15.1 0 0 0 6.6 6.6l2.2-2.2c.3-.3.7-.4 1-.2 1.1.4 2.3.6 3.6.6.6 0 1 .4 1 1V20c0 .6-.4 1-1 1A17 17 0 0 1 3 4c0-.6.4-1 1-1h3.5c.6 0 1 .4 1 1 0 1.3.2 2.5.6 3.6.1.3 0 .7-.2 1z"/></svg>
        415 903 2276
      </li>
      <li>
        <svg viewBox="0 0 24 24" aria-hidden="true"><path d="M2 5h20v14H2z M3.5 6.5v.4L12 13l8.5-6.1v-.4z" fill-rule="evenodd"/></svg>
        info@brightpawobedience.example
      </li>
      <li>
        <svg viewBox="0 0 24 24" aria-hidden="true"><circle cx="12" cy="12" r="10"/><path d="M7 6c2 1 3 3 2 5s-3 2-3 4M14 4c-1 2 1 3 3 3s3 2 2 4M13 20c0-2 2-3 3-5" stroke="#fff" stroke-width="1.6" fill="none"/></svg>
        brightpawobedience.example
      </li>
    </ul>
  </section>

  <section class="card card-back">
    <div class="back-mark">
      <span class="square"></span>
      <span>Brightpaw<br>Obedience</span>
    </div>
    <p class="tagline">“Good manners, happy dogs, one walk at a time.”</p>
  </section>
</body>
</html>
```